Step Forth Daily newsletter - Mail Chimp

Step Forth Daily - Empowering Life Coach needs Mail Chimp Newsletter Template. This is a newsletter I will send out monthly to current clients and prospective clients to offer (hopefully) inspiring and uplifting content AND to give info and dates of my upcoming workshops and retreats.

I have attached a word document with all of the different sections of the mail chimp template I would like to have - and hte actual content for the first newsletter.

I'd like to look uplifting, fun, inspiring.

I also need it to be easy for me to use to update in the future :)

Target Market(s)

Women - moms

Industry/Entity Type

Life Coaching

Requirements
Nice to have
• Color theme to match my "Step Forth Daily" logo

```html
<!DOCTYPE html>
<html lang="en">
<head>
<meta charset="utf-8">
<title>Step Forth Daily – Newsletter</title>
<link href="https://fonts.googleapis.com/css2?family=Lato:wght@400;700;900&family=Crimson+Text:ital,wght@0,400;1,400&display=swap" rel="stylesheet">
<style>
:root{
  --purple:#5a1f78;
  --orange:#f7931e;
  --pink:#c2185b;
  --blue:#2a9ad6;
  --green:#7cc242;
  --teal:#1a9fd9;
  --ink:#2f2f2f;
  --white:#ffffff;
  --grey:#d6d6d6;
}
*{box-sizing:border-box;margin:0;padding:0}
html,body{width:1200px;height:4905px;overflow:hidden;background:var(--white)}
body{font-family:'Lato',sans-serif;color:var(--ink);font-size:21px;line-height:36px;position:relative}
.serif{font-family:'Crimson Text',serif}
.section{position:absolute;left:0;width:1200px}

.header{top:0;height:165px}
.brand{position:absolute;left:62px;top:50px;display:flex;align-items:center;gap:14px}
.brand-dot{width:38px;height:38px;border-radius:50%;background:var(--orange)}
.brand-name{font-family:'Crimson Text',serif;font-size:46px;color:var(--purple)}
.follow{position:absolute;right:40px;top:50px;display:flex;align-items:center;gap:22px;font-weight:700;font-size:22px;color:var(--purple)}
.follow span.icon{width:30px;height:30px;border-radius:50%;background:var(--teal)}

.hero{top:165px;height:425px;background:linear-gradient(180deg,#f6c067 0%,#f29a2c 55%,#b3561a 100%)}

.intro{top:590px;height:715px}
.intro-photo{position:absolute;left:40px;top:70px;width:262px;height:200px;background:linear-gradient(135deg,#2a6fb5,#f0c419 60%,#e8772e)}
.intro-text{position:absolute;left:335px;top:60px;width:830px}
.intro-text h2{font-family:'Crimson Text',serif;font-style:italic;font-weight:400;color:var(--pink);font-size:36px;line-height:46px;margin-bottom:6px}
.intro-text p{margin-bottom:0}
.sign{margin-top:20px;font-weight:700}
.sign-name{font-family:'Crimson Text',serif;font-style:italic;color:var(--teal);font-size:38px;line-height:42px}

.tips{top:1305px;height:1215px;background:var(--purple);color:var(--white);padding:80px 40px 0 40px}
.tips h2{font-family:'Crimson Text',serif;font-weight:400;font-size:46px;line-height:56px;margin-bottom:24px}
.tips h3{font-family:'Crimson Text',serif;font-style:italic;font-weight:400;color:var(--orange);font-size:38px;line-height:44px;margin:22px 0 16px}
.tips p{font-size:20px;line-height:36px;margin-bottom:14px}
.tips ul{list-style:none;margin:6px 0 14px}
.tips li{display:flex;align-items:center;gap:18px;font-size:20px;line-height:46px}

.more{top:2520px;height:620px}
.more-copy{position:absolute;left:18px;top:80px;width:420px}
.more-copy h2{font-family:'Crimson Text',serif;font-weight:400;font-size:50px;line-height:60px;color:var(--ink);margin-bottom:20px}
.more-copy p{font-family:'Crimson Text',serif;color:var(--purple);font-size:32px;line-height:40px}
.quote-a{position:absolute;left:452px;top:85px;width:290px;height:445px;background:linear-gradient(180deg,#b48a56,#5a4630)}
.quote-b{position:absolute;left:750px;top:85px;width:435px;height:445px;background:linear-gradient(180deg,#ecdcd0,#b9a7a0)}

.books{top:3140px;height:440px;background:var(--blue);color:var(--white)}
.book-art{position:absolute;left:70px;top:60px;width:280px;height:300px;background:linear-gradient(135deg,#f2f2f2,#bdbdbd)}
.books-copy{position:absolute;left:490px;top:70px;width:690px}
.books-copy h2{font-family:'Crimson Text',serif;font-weight:400;font-size:46px;line-height:56px;margin-bottom:16px}
.books-copy p{font-size:20px;line-height:34px}

.events{top:3580px;height:770px}
.events-box{position:absolute;left:40px;top:60px;width:1140px;height:620px;border:4px solid var(--grey)}
.events-side{position:absolute;left:0;top:0;width:395px;height:612px;background:var(--green);color:var(--white);text-align:center;padding-top:50px}
.side-name{font-family:'Crimson Text',serif;font-size:38px;line-height:44px;margin-bottom:28px}
.side-label{color:#333;font-weight:700;font-size:22px;margin-bottom:4px}
.side-info{font-weight:700;font-size:22px;line-height:34px}
.events-copy{position:absolute;left:440px;top:30px;width:670px}
.events-copy h2{font-family:'Crimson Text',serif;font-weight:400;color:var(--pink);font-size:46px;line-height:56px;margin-bottom:12px}
.events-copy p{font-size:20px;line-height:34px;margin-bottom:18px}

.closing{top:4350px;height:450px;background:var(--blue);color:var(--white)}
.closing-copy{position:absolute;left:78px;top:80px;font-family:'Crimson Text',serif;font-size:44px;line-height:54px}
.closing-photo{position:absolute;left:760px;top:40px;width:365px;height:290px;background:linear-gradient(135deg,#e0e0e0,#5c5c5c);border:4px solid var(--white)}

.footer{top:4820px;height:85px;text-align:center;font-size:19px;color:#555}
.wedge{position:absolute;left:0;width:1200px}
</style>
</head>
<body>

<header class="section header">
  <div class="brand"><span class="brand-dot"></span><span class="brand-name">Step Forth Daily</span></div>
  <div class="follow">Follow Us: <span class="icon"></span><span class="icon"></span><span class="icon"></span><span class="icon"></span></div>
</header>

<div class="section hero" role="img" aria-label="Hands forming a heart shape against a glowing sunset sky"></div>

<section class="section intro">
  <div class="intro-photo" role="img" aria-label="Coach relaxing on a yellow float in a pool"></div>
  <div class="intro-text">
    <h2>Hello Friends!!</h2>
    <p>I am excited to (hopefully) add a little love to your in-box with this newsletter. I love connecting with moms and helping them find tools to make their lives happier, more intentional, and more fun and this is a new way to do that! If you don't know me well, I am a certified Open Horizons Trainer and I lead coaching groups for moms. My OH workshops and Bright Moms Circle have the goal of fostering connections between amazing women and empowering moms with tools to build lives they are enthusiastic about living, on purpose – and that will be the goal of this newsletter, as well! I hope you find something useful and helpful and enjoy receiving this info (and if not, feel free to unsubscribe and my feelings will not be hurt!</p>
    <p class="sign">With love,</p>
    <p class="sign-name">Dana</p>
  </div>
  <svg class="wedge" style="bottom:0" width="1200" height="40" viewBox="0 0 1200 40"><polygon points="0,40 1200,0 1200,40" fill="#f7931e"/></svg>
</section>

<section class="section tips">
  <h2>Step Forth Daily Tips &amp; Tools:</h2>
  <h3 style="margin-top:0">Building Happiness</h3>
  <p>I firmly believe that thinking about your happiness is important and that happiness itself is a worthwhile goal! If you think about all the things you focus on in your life and all the goals you set for yourself, all of those things are leading you toward feeling happier. Happiness, in the end, is the ultimate goal.</p>
  <p>Of course, what makes each person happy is totally different – and that's awesome and one part of what makes life fun and exciting! Many happiness experts and authors note that the key ingredients in our lives that will make us happier are pursuing 2 categories:</p>
  <ul>
    <li><svg width="22" height="18" viewBox="0 0 22 18"><path d="M2 9l6 6L20 2" fill="none" stroke="#fff" stroke-width="4"/></svg>Things that bring us pleasure (positive emotions) and</li>
    <li><svg width="22" height="18" viewBox="0 0 22 18"><path d="M2 9l6 6L20 2" fill="none" stroke="#fff" stroke-width="4"/></svg>Things that bring us meaning &amp; fulfillment</li>
  </ul>
  <p>Give yourself a minute to think about (it's extra powerful if you write it down!) what makes YOU happy.</p>
  <h3>What are things that make you feel happy / provide you with pleasure (little and big things)?</h3>
  <p>For me: joking &amp; laughing with my kids &amp; husband, petting with my dog, sitting with a soft blanket and a book, my first sip of coffee in the morning, walking in nature, travelling, scuba diving, exercise classes, making my friends laugh.</p>
  <h3>What are things that are meaningful to you / make you feel fulfilled (little and big things)?</h3>
  <p>For me: teaching Open Horizons workshops, spending quality time with my family, making gratitude lists, volunteering, leading moms' coaching groups, making my kids breakfast.</p>
  <svg class="wedge" style="bottom:0" width="1200" height="40" viewBox="0 0 1200 40"><polygon points="0,40 1200,0 1200,40" fill="#f7931e"/></svg>
</section>

<section class="section more">
  <div class="more-copy">
    <h2>How could you add more of those things that bring you happiness to your days?</h2>
    <p>Try to add 1 or 2 of those things per week and see how your happiness increases! You are worth it!</p>
  </div>
  <div class="quote-a" role="img" aria-label="Inspirational quote card about designing happiness in the present"></div>
  <div class="quote-b" role="img" aria-label="Inspirational quote card about happiness in simple things"></div>
</section>

<section class="section books">
  <div class="book-art" role="img" aria-label="Book cover placeholder"></div>
  <div class="books-copy">
    <h2>Empowering Books</h2>
    <p>I love to read uplifting, inspiring material. Each newsletter, I'll suggest a few books that I've enjoyed!<br>The Joy Ledger by Mara Ellison<br>Bold and Bright. How to Stop Doubting Your Strength and Start Living a Vivid Life" by Lena Harwood</p>
  </div>
</section>

<section class="section events">
  <div class="events-box">
    <div class="events-side">
      <div class="side-name">Open Horizons</div>
      <div class="side-label">Dates:</div>
      <div class="side-info">3 morning workshop<br>September 27, October 4,<br>October 11<br>9:30 – 12:30<br>Dana's home in Maple<br>Ridge</div>
      <div class="side-label" style="margin-top:18px">Interested?</div>
      <div class="side-info">Email Me:<br>dana@stepforthdaily.com</div>
    </div>
    <div class="events-copy">
      <h2>Upcoming Events</h2>
      <p>I lead an Open Horizons Workshop 2-3 times per year. The next one is coming up in September/October. More details to come – but here is a little info…</p>
      <p>Moms - Back to School, Back to You!<br>In September, the kids will be going back to school and you can spend time focusing on YOU. Let this be the year where you take time to focus on yourself so that you can feel amazing, focused, fulfilled, purposeful, and happier! Take the time to learn some simple tools to help you live a life you love, deliberately, instead of just juggling what comes at you and juggling your to-do list. In this workshop, you will be empowered to build a life you love.</p>
    </div>
  </div>
</section>

<section class="section closing">
  <svg class="wedge" style="top:0" width="1200" height="40" viewBox="0 0 1200 40"><polygon points="0,0 1200,0 1200,40" fill="#f7931e"/></svg>
  <div class="closing-copy">Enjoy the rest of Summer Break!<br>Savor each amazing day!<br>How can you add a little more<br>HAPPY to your August??<br>Make the choice and do it!</div>
  <div class="closing-photo" role="img" aria-label="Black and white quote card about choosing happiness"></div>
  <svg class="wedge" style="bottom:0" width="1200" height="40" viewBox="0 0 1200 40"><polygon points="0,40 1200,0 1200,40" fill="#f7931e"/></svg>
</section>

<footer class="section footer">Copyright © 2018 Company Name All Right Reserved</footer>

</body>
</html>
```